New Business Card Design for Manufacturing

We are an engineering/manufacturing company that offers Advanced machining/assembly/engineering services, as well as innovative products for the heavy duty engine cooling markets.

We are looking to get a new business card designed that is clean and modern looking, but still fits the wide range of technical/skilled work we do.

- We hope to use this design as the base for other design work in new Presentations, web, and print work.

Industry/Entity Type

Engineering

Contact Information for Business Card

Our preferred color of blue is (RGB) 22/71/159 but can vary slightly from that color. Our content will be our Logo and full company name (Vantrell Forge Works, Inc.), company address, name, job title, phone number with extension, cell number, fax number, website, and email address on the cards.
We'd like the full company name next to the logo, but we are open to other interpretations of that layout.
Preferably, we would like the back side to be clean with just our logo, and the front to contain all of the contact information.

Colors
2f74b4
0355a3
85abd2

Requirements
Must have
• - Logo, company name, needed content - We are open to interpretation beyond that.
• - Standard size business card.
• - Horizontal orientation.
• - Enough space for lengthy names / job titles (for example, a job title could read "Directory of Human Resources" or "V.P. of Governmental Affairs"). We need this to look clean, whether the title be short (CEO) or long (as described above).

```html
<!DOCTYPE html>
<html lang="en">
<head>
<meta charset="utf-8">
<title>Vantrell Forge Works – Business Card</title>
<link rel="stylesheet" href="https://fonts.googleapis.com/css2?family=Open+Sans:wght@400;600;700;800&display=swap">
<style>
  :root{
    --brand-blue:#16479f;
    --band-blue:#1856a6;
    --card-grey:#7c8084;
    --card-grey-light:#8a8e92;
    --divider-grey:#8d9195;
    --paper:#ffffff;
    --page:#eceae6;
    --ink-light:#ffffff;
  }
  *{margin:0;padding:0;box-sizing:border-box}
  html,body{width:1200px;height:900px;overflow:hidden}
  body{background:var(--page);font-family:"Open Sans",Arial,sans-serif;position:relative}

  .card{position:absolute;left:320px;width:560px;height:320px;overflow:hidden;box-shadow:0 2px 6px rgba(0,0,0,.18)}

  /* back side */
  .card-back{top:100px;background:linear-gradient(180deg,var(--card-grey-light),var(--card-grey));
    display:flex;align-items:center;justify-content:center}
  .wordmark{display:flex;align-items:center;gap:12px;color:var(--brand-blue);font-weight:800;
    font-size:78px;line-height:1;letter-spacing:2px}
  .wordmark .mark-square{width:22px;height:22px;background:var(--brand-blue)}

  /* front side */
  .card-front{top:470px;background:var(--paper)}
  .front-head{position:absolute;left:0;top:0;width:100%;height:170px;display:flex;align-items:center;padding-left:72px;gap:18px}
  .front-head .wordmark{font-size:72px}
  .company-name{color:var(--brand-blue);font-weight:800;font-size:15px;line-height:1.05;text-transform:uppercase;letter-spacing:.3px}
  .company-name small{font-size:8px;font-weight:700;margin-left:3px}

  .divider{position:absolute;left:0;top:170px;width:100%;height:5px;background:var(--divider-grey)}
  .pointer{position:absolute;left:68px;top:174px}
  .contact-band{position:absolute;left:0;top:175px;width:100%;height:145px;background:var(--band-blue);color:var(--ink-light)}
  .person{position:absolute;left:34px;top:26px;font-size:14px;line-height:1.3}
  .person .name{font-weight:700;font-size:18px;text-transform:uppercase;letter-spacing:.3px;line-height:1.15}
  .person .role,.person .address{font-weight:400;font-size:14px}

  .contacts{position:absolute;right:22px;top:14px;list-style:none;font-size:12px;line-height:1.55;text-align:right}
  .contacts li{display:flex;align-items:center;justify-content:flex-end;gap:5px}
  .contacts svg{width:10px;height:10px;fill:var(--ink-light)}
</style>
</head>
<body>

  <section class="card card-back" aria-label="Card back">
    <div class="wordmark"><span class="mark-square"></span>VFW</div>
  </section>

  <section class="card card-front" aria-label="Card front">
    <header class="front-head">
      <div class="wordmark">VFW</div>
      <div class="company-name">Vantrell<br>Forge<br>Works<small>Inc</small></div>
    </header>

    <div class="divider"></div>
    <div class="contact-band">
      <div class="person">
        <div class="name">Dorian Halvex</div>
        <div class="role">Managing Director</div>
        <div class="address">1234, Address GoesHere<br>Country name, 12345</div>
      </div>
      <ul class="contacts">
        <li>(044)987650123
          <svg viewBox="0 0 10 10"><path d="M1 3c0-1 1-2 4-2s4 1 4 2v1H7V3H3v1H1z M2 5h6v4H2z"/></svg></li>
        <li>(044)987650123
          <svg viewBox="0 0 10 10"><path d="M3 0h4a1 1 0 0 1 1 1v8a1 1 0 0 1-1 1H3a1 1 0 0 1-1-1V1a1 1 0 0 1 1-1zM3 1.5v6h4v-6z"/></svg></li>
        <li>(044)987650123
          <svg viewBox="0 0 10 10"><path d="M3 0h4v3H3zM1 3h8v5H7v2H3V8H1zM4 6v3h2V6z"/></svg></li>
        <li>info@vantrellforge.com
          <svg viewBox="0 0 10 10"><path d="M0 2h10v6H0zM1 3l4 3 4-3v-.2H1z" fill-rule="evenodd"/></svg></li>
      </ul>
    </div>
    <svg class="pointer" width="30" height="14" viewBox="0 0 30 14" aria-hidden="true">
      <polygon points="0,0 30,0 15,14" fill="var(--divider-grey)"/>
    </svg>
  </section>

</body>
</html>
```